Coastal Gin Label Design

We are needing a nautical/coastal themed label for our upcoming gin release.

We have saltbush, cucumber, juniper, and quandong being used in this gin.

Name of the Gin; Harbour Moons

The logo attached is the company logo, but doesn't have to be used on the front of the label, ie it can just be the name Fernwhistle somewhere on the front.
Bottle specs attached as well so you can accurately represent the bottle- this bottle is also clear.

Target Market(s)

Women 25- 45

Font styles to use
Serif
Decorative

Colors
d5edf4
86cae7
33a6d7
86cfc6
cfeae6
ffffff
f6faec
ecf7fb
fefeff

Requirements
Must have
• Ocean/Coastal vibe to the label
Nice to have
• Blues,Whites clean and crisp
Should not have
• No generic word art look to it.
A dark mood

```html
<!DOCTYPE html>
<html lang="en">
<head>
<meta charset="utf-8">
<title>Harbour Moons Gin – Label</title>
<link rel="stylesheet" href="https://fonts.googleapis.com/css2?family=Arvo:wght@400;700&family=Cormorant+SC:wght@600&display=swap">
<style>
  :root {
    --page: #e6ecf1;
    --label: #f2f4f4;
    --panel: #eceeee;
    --edge: #86cfc6;
    --frame: #9ab7b8;
    --title-blue: #2f93c4;
    --sea-deep: #4f7f86;
    --sea-mid: #7fa9ae;
    --sea-light: #b7d0d0;
    --sand: #cfc3b1;
    --sand-light: #ddd5c7;
    --ink: #2a2a2a;
    --wave-icon: #a9c7c9;
  }
  * { box-sizing: border-box; margin: 0; padding: 0; }
  html, body { width: 794px; height: 1200px; overflow: hidden; }
  body { background: var(--page); position: relative; }

  .label {
    position: absolute;
    left: 47px; top: 275px;
    width: 700px; height: 650px;
    background: var(--label);
  }
  .label__edge { position: absolute; inset: -7px; width: 714px; height: 664px; pointer-events: none; }

  .label__frame-top {
    position: absolute; left: 31px; right: 35px; top: 28px;
    height: 4px; background: var(--frame);
  }
  .label__frame-left, .label__frame-right {
    position: absolute; top: 28px; width: 4px; height: 284px; background: var(--frame);
  }
  .label__frame-left { left: 31px; }
  .label__frame-right { right: 35px; }

  .brand {
    position: absolute; top: 98px; left: 0; right: 0;
    text-align: center;
    font-family: "Cormorant SC", Georgia, serif;
    font-weight: 600; font-size: 22px; letter-spacing: 2px;
    color: var(--ink);
  }

  .seascape {
    position: absolute; left: 0; right: 0; top: 300px; bottom: 0;
    background: linear-gradient(180deg,
      var(--sea-light) 0%, var(--sea-mid) 14%, var(--sea-deep) 40%,
      var(--sea-mid) 58%, var(--sand-light) 68%, var(--sand) 100%);
  }

  .name-panel {
    position: absolute; left: 206px; width: 281px; top: 300px; height: 287px;
    background: var(--panel);
  }

  .gin-name {
    position: absolute; top: 200px; left: 0; right: 0;
    text-align: center;
    font-family: "Arvo", Georgia, serif;
    font-weight: 700; font-size: 60px; line-height: 66px;
    color: var(--title-blue);
    letter-spacing: 1px;
  }

  .wave-mark {
    position: absolute; left: 266px; top: 400px; width: 162px; height: 40px;
    background: var(--wave-icon); opacity: .55; border-radius: 20px;
  }

  .gin-type {
    position: absolute; top: 494px; left: 206px; width: 281px;
    text-align: center;
    font-family: "Arvo", Georgia, serif;
    font-weight: 700; font-size: 64px; line-height: 72px;
    color: var(--title-blue);
  }

  .volume, .strength {
    position: absolute; top: 583px;
    font-family: "Arvo", Georgia, serif;
    font-weight: 700; font-size: 18px;
    color: var(--ink);
  }
  .volume { left: 62px; }
  .strength { right: 56px; }
</style>
</head>
<body>
  <main class="label">
    <div class="seascape" role="img" aria-label="Watercolour painting of ocean waves breaking onto a sandy shore"></div>

    <div class="label__frame-top"></div>
    <div class="label__frame-left"></div>
    <div class="label__frame-right"></div>

    <div class="name-panel"></div>

    <p class="brand">Fernwhistle</p>

    <h1 class="gin-name">HARBOUR<br>MOONS</h1>

    <div class="wave-mark" role="img" aria-label="Small cloud and wave motif"></div>

    <p class="gin-type">Gin</p>

    <p class="volume">700 ml</p>
    <p class="strength">40% alc/vol</p>

    <svg class="label__edge" viewBox="0 0 714 664" aria-hidden="true">
      <defs>
        <pattern id="zigzag-h" width="10" height="7" patternUnits="userSpaceOnUse">
          <path d="M0 7 L5 0 L10 7 Z" fill="#86cfc6"/>
        </pattern>
        <pattern id="zigzag-v" width="7" height="10" patternUnits="userSpaceOnUse">
          <path d="M7 0 L0 5 L7 10 Z" fill="#86cfc6"/>
        </pattern>
      </defs>
      <rect x="7" y="0" width="700" height="7" fill="url(#zigzag-h)"/>
      <rect x="7" y="657" width="700" height="7" fill="url(#zigzag-h)" transform="rotate(180 357 660.5)"/>
      <rect x="0" y="7" width="7" height="650" fill="url(#zigzag-v)"/>
      <rect x="707" y="7" width="7" height="650" fill="url(#zigzag-v)" transform="rotate(180 710.5 332)"/>
      <rect x="7" y="7" width="700" height="650" fill="none" stroke="#86cfc6" stroke-width="2"/>
    </svg>
  </main>
</body>
</html>
```